Velvet Lantern rebranding my business with a new business card

I have my new logo and now I need a refresher on my business cards. I really want something fun and fresh. I like black background or anything to make the color pop.
Logo
Name: Velvet Lantern
Contact Info as stated below:
Mira Pellow
555-013-4762
Logo
Name: Velvet Lantern
Mira Pellow
555-013-4762
vl.link/VelvetLanternbyMira
Instagram: @VelvetLanternbyMira

Industry/Entity Type

Business

Contact Information for Business Card

double-sided. Logo on one side. Contact info on the other.

Requirements
Must have
• Logo
• Name: Velvet Lantern
• Contact Info as stated below:
• Mira Pellow
• 555-013-4762
• vl.link/VelvetLanternbyMira
• vl.link/VelvetLanternbyMira

```html
<!DOCTYPE html>
<html lang="en">
<head>
<meta charset="utf-8">
<title>Velvet Lantern — Business Card</title>
<link href="https://fonts.googleapis.com/css2?family=Source+Sans+3:wght@400;600&display=swap" rel="stylesheet">
<style>
  :root {
    --backdrop-top: #6a6a6a;
    --backdrop-bottom: #3f3f3f;
    --card-front: #ffffff;
    --card-back: #111111;
    --accent-pink: #ef8c96;
    --accent-rule: #e0737d;
    --logo-pink: #d884d4;
    --text-dark: #2a2a2a;
  }
  * { margin: 0; padding: 0; box-sizing: border-box; }
  html, body { width: 1200px; height: 900px; overflow: hidden; }
  body {
    position: relative;
    background: linear-gradient(to bottom, var(--backdrop-top), var(--backdrop-bottom));
    font-family: "Source Sans 3", "Myriad Pro", Arial, sans-serif;
  }
  .card {
    position: absolute;
    top: 306px;
    width: 440px;
    height: 271px;
    border-radius: 12px;
    box-shadow: 0 2px 6px rgba(0,0,0,0.35);
  }
  .card--front { left: 149px; background: var(--card-front); }
  .card--back { left: 608px; background: var(--card-back); }

  .brand-mark {
    position: absolute;
    display: flex;
    align-items: center;
    justify-content: center;
    text-align: center;
    font-weight: 600;
    font-size: 26px;
    line-height: 1.05;
  }
  .card--front .brand-mark {
    left: 30px; top: 52px; width: 162px; height: 168px;
    color: var(--accent-pink);
  }
  .card--back .brand-mark {
    left: 140px; top: 52px; width: 162px; height: 168px;
    color: var(--logo-pink);
  }

  .divider {
    position: absolute;
    left: 216px; top: 83px;
    width: 2px; height: 102px;
    background: var(--accent-rule);
  }
  .holder-name {
    position: absolute;
    left: 236px; top: 78px;
    font-size: 18px;
    font-weight: 400;
    line-height: 22px;
    color: var(--accent-pink);
    text-transform: uppercase;
  }
  .contact-list {
    position: absolute;
    left: 234px; top: 149px;
    list-style: none;
  }
  .contact-list li {
    display: flex;
    align-items: center;
    height: 20px;
    font-size: 13px;
    color: var(--text-dark);
  }
  .contact-list svg { width: 16px; height: 16px; margin-right: 7px; flex: none; }
</style>
</head>
<body>
  <section class="card card--front" aria-label="Business card front">
    <div class="brand-mark">Velvet<br>Lantern</div>
    <div class="divider"></div>
    <h1 class="holder-name">Mira Pellow</h1>
    <ul class="contact-list">
      <li>
        <svg viewBox="0 0 16 16" aria-hidden="true">
          <circle cx="8" cy="8" r="8" fill="var(--accent-pink)"/>
          <path d="M5.2 4.2c.4-.3.8-.2 1 .2l.7 1.3c.2.4.1.7-.2 1l-.5.4c.4.9 1.1 1.6 2 2l.4-.5c.3-.3.6-.4 1-.2l1.3.7c.4.2.5.6.2 1l-.6.8c-.4.4-1 .5-1.6.3-2-.8-3.5-2.3-4.3-4.3-.2-.6-.1-1.2.3-1.6z" fill="#ffffff"/>
        </svg>
        555-013-4762
      </li>
      <li>
        <svg viewBox="0 0 16 16" aria-hidden="true">
          <circle cx="8" cy="8" r="8" fill="var(--accent-pink)"/>
        </svg>
        vl.link/VelvetLanternbyMira
      </li>
    </ul>
  </section>

  <section class="card card--back" aria-label="Business card back">
    <div class="brand-mark">Velvet<br>Lantern</div>
  </section>
</body>
</html>
```